Cloud Based Bookkeeping Website for Florists (Flower Shops)

We need a single page responsive website for a bookkeeping firm specializing in the floral industry. Our business model is based on the cloud and a goal is to attain floral clients from around the country, not only local.

Currently, we are attracted to flat illustration designs, but are concerned that they appear to informal or unprofessional. This webdesign should communicate professionalism, yet approachable, bright, attractive and modern.

The color scheme and overall design should match our designed logo, which is attached, and icon sets. We are open to new icon ideas and layout design, other than the layout we prepared and attached.

The attached layout we prepared has a holding place for a video at the top section. We own the video and can provide at a later time to insert. There is another secondary holding place for an explanation video, which we may or may not need, depending on the design your submit.

Lastly, I want to reiterate that we are open to new layout ideas.

Target Market(s)

Florists, Flower Shops

Industry/Entity Type

Bookkeeper

Number of Pages Required

2 page

Font styles to use
Sans Serif

Requirements
Must have
• Each section should be full width and screen height.
• Full page/section scrolling
• A price table
• A scrolling or fixed section displaying the third party app we work with.
• A blog page and a scrolling carousel displaying recent blog posts.
• Services section should be the six listed, but expandable to add more.
• A lead generation page, where clients can add attachments
• Must be a WordPress design so owner can easily modify and edit in the future
• Must be able to accommodate java script snippets in the header.
Nice to have
• A fixed "Contact Us" tab on the right side of the page that will lead to a contact form.

```html
<!DOCTYPE html>
<html lang="en">
<head>
<meta charset="utf-8">
<title>Petalbooks — Bookkeeping for Florists</title>
<link href="https://fonts.googleapis.com/css2?family=Montserrat:wght@400;600;700;800&family=Open+Sans:wght@400;600;700&display=swap" rel="stylesheet">
<style>
:root{
  --orange:#e8662a;
  --orange-soft:#fbe5d8;
  --ink:#262626;
  --text:#5a5a5a;
  --muted:#8a8a8a;
  --line:#e4e4e4;
  --grey-bg:#f2f2f2;
  --dark:#2b2b2b;
  --darker:#1f1f1f;
  --white:#fff;
}
*{box-sizing:border-box;margin:0;padding:0}
html,body{width:1200px;height:5128px;overflow:hidden}
body{font-family:"Open Sans",Arial,sans-serif;color:var(--text);background:var(--white);font-size:13px;line-height:1.7}
h2,h3,h4,.btn,.nav{font-family:"Montserrat",Arial,sans-serif}
section{position:relative;width:1200px;overflow:hidden}
.section-title{font-size:28px;font-weight:800;color:var(--ink);text-align:center;letter-spacing:.5px;text-transform:uppercase}
.section-title span{color:var(--orange)}
.lead{max-width:1000px;margin:0 auto;text-align:center;font-size:12.5px;color:var(--text)}
.lead p{margin-bottom:14px}
.btn-row{display:flex;justify-content:center;gap:22px}
.btn{display:inline-block;border:1.5px solid var(--orange);color:var(--orange);font-size:14px;font-weight:600;padding:8px 30px;background:var(--white)}

/* hero */
.hero{height:615px;background:linear-gradient(120deg,#3a3a3a 0%,#6b6b6b 35%,#cfcfcf 55%,#8c8c8c 75%,#2f2f2f 100%)}
.hero-photo{position:absolute;inset:0}
.hero-shade{position:absolute;inset:0;background:rgba(0,0,0,.35)}
.brand{position:absolute;left:30px;top:12px;color:var(--white)}
.brand-name{font-family:"Montserrat",Arial,sans-serif;font-size:22px;font-weight:700;color:var(--orange);display:flex;align-items:center;gap:8px}
.brand-name i{display:block;width:16px;height:16px;background:var(--orange)}
.brand-tag{font-size:10px;color:#ddd;margin-left:24px}
.nav{position:absolute;right:40px;top:12px;text-align:right;color:var(--white)}
.nav-main{font-size:14px;font-weight:600}
.nav-sub{font-size:11px;margin-top:4px}
.nav-sub span{margin-left:20px}
.play{position:absolute;left:580px;top:300px}
.hero-title{position:absolute;top:365px;width:100%;text-align:center;color:var(--white);font-family:"Montserrat",Arial,sans-serif;font-size:34px;font-weight:800;letter-spacing:.5px}

/* why */
.why{height:375px;padding-top:48px}
.why .lead{margin-top:28px}
/* how */
.how{height:600px;background:var(--grey-bg);padding-top:50px}
.video{width:512px;height:206px;margin:26px auto 30px;background:linear-gradient(90deg,#1c1a17,#4a3b2c 50%,#1c1a17);position:relative}
.video svg{position:absolute;left:236px;top:83px}
.how .lead{margin-bottom:12px}

/* services */
.services{height:770px;padding-top:58px}
.service-grid{width:1000px;margin:40px auto 0;display:grid;grid-template-columns:repeat(3,1fr);gap:26px 20px}
.service-card{border:1px solid var(--line);height:230px;padding:24px 22px;text-align:center;box-shadow:0 2px 6px rgba(0,0,0,.05)}
.service-icon{width:70px;height:70px;margin:0 auto 14px;background:linear-gradient(135deg,#f2c9b2,#e8662a 60%,#444);border-radius:6px}
.service-card h3{color:var(--orange);font-size:17px;font-weight:700;margin-bottom:6px}
.service-card p{font-size:12px;line-height:1.5}
.services .btn-row{margin-top:40px}

/* outsourced */
.outsourced{height:290px;background:var(--grey-bg);padding-top:40px}
.outsourced .lead{margin-top:18px;font-size:12px}
.outsourced .lead p{margin-bottom:10px}

/* cost */
.cost{height:495px;padding-top:44px}
.cost .lead{margin-top:18px}
.cost-items{display:flex;justify-content:center;gap:70px;margin:18px 0 22px}
.cost-item{width:170px;text-align:center;font-size:13px;color:var(--ink)}
.cost-icon{width:80px;height:70px;margin:0 auto 10px;background:linear-gradient(135deg,#555,#e8662a);border-radius:6px}

/* pricing */
.pricing{height:480px;padding-top:20px}
.price-grid{display:flex;justify-content:center;gap:22px;margin-top:24px}
.price-card{width:330px;height:370px;border:1px solid var(--line);box-shadow:0 2px 8px rgba(0,0,0,.08);text-align:center}
.price-head{height:135px;display:flex;align-items:center;justify-content:center;color:var(--white);font-family:"Montserrat",Arial,sans-serif;font-size:26px;font-weight:800}
.basic{background:linear-gradient(135deg,#7a2a1a,#c9573a)}
.standard{background:linear-gradient(135deg,#6c6c6c,#cfcfcf)}
.premium{background:linear-gradient(135deg,#2a3a5a,#a03030)}
.price-card ul{list-style:none;font-size:13px;color:var(--text);padding:14px 0 10px;line-height:1.55}
.buy{display:inline-block;background:var(--darker);color:var(--white);font-family:"Montserrat",Arial,sans-serif;font-size:11px;font-weight:700;padding:6px 28px}

/* lead gen */
.convince{height:530px;padding-top:20px}
.convince .lead{margin-top:14px;font-size:12px}
.convince .lead p{margin-bottom:6px}
.quote-form{position:absolute;left:190px;top:162px;width:240px;height:345px;background:var(--orange-soft);padding:22px 20px}
.quote-form .field{height:30px;background:var(--white);border:1px solid #eed3c4;margin-bottom:20px;font-size:11px;color:var(--muted);padding:6px 10px;line-height:1.6}
.quote-form .submit{background:var(--orange);color:var(--white);text-align:center;font-family:"Montserrat",Arial,sans-serif;font-size:14px;font-weight:600;height:30px;line-height:30px;margin:0 20px}
.dropzone{position:absolute;left:565px;top:222px;width:445px;height:170px;background:var(--orange);display:flex;align-items:center;justify-content:center;color:var(--white);font-family:"Montserrat",Arial,sans-serif;font-size:19px;font-weight:600}

/* partners */
.partners{height:190px;display:flex;justify-content:center;align-items:center;gap:130px}
.partner{font-family:"Open Sans",Arial,sans-serif;font-size:26px;font-weight:700;color:#2a4f8a;display:flex;align-items:center;gap:8px}
.partner i{display:block;width:22px;height:22px;border-radius:50%;background:#2a4f8a}

/* blog */
.blog{height:477px;padding:24px 60px 0}
.blog-head{display:flex;justify-content:space-between;align-items:center}
.blog-head h2{color:var(--orange);font-size:22px;font-weight:800}
.dots{display:flex;gap:6px}
.dots i{width:11px;height:11px;border-radius:50%;background:#bbb;display:block}
.dots i:first-child{background:var(--orange)}
.blog-grid{display:flex;justify-content:space-between;margin-top:20px;padding:0 40px}
.post{width:310px;height:345px;box-shadow:0 3px 10px rgba(0,0,0,.12);background:var(--white)}
.post-img{height:150px}
.p1{background:linear-gradient(135deg,#f1e6dc,#b84a3a)}
.p2{background:linear-gradient(90deg,#222,#777 30%,#ddd 50%,#555 70%,#222)}
.p3{background:linear-gradient(135deg,#f5f5f5,#9a9a9a)}
.post-body{padding:14px 18px}
.post h4{font-size:14px;font-weight:700;color:var(--ink);margin-bottom:6px}
.post p{font-size:11px;line-height:1.5;margin-bottom:12px}
.read{display:inline-block;background:var(--orange);color:var(--white);font-family:"Montserrat",Arial,sans-serif;font-size:12px;font-weight:700;padding:6px 18px}

/* footer */
.footer{height:274px;background:var(--dark);display:flex;gap:0;padding:40px 90px 0;color:#bdbdbd}
.footer-col{width:255px}
.footer-col h4{color:var(--white);font-size:15px;font-weight:600;margin-bottom:10px}
.footer-col li{list-style:none;font-size:12px;line-height:2}
.subscribe{width:190px;height:26px;background:#f0f0f0;margin-bottom:16px;display:flex;justify-content:space-between;align-items:center;padding:0 8px;font-size:10px;color:var(--muted)}
.socials{display:flex;gap:8px}
.socials i{display:block;width:24px;height:24px;border:1.5px solid #cfcfcf;border-radius:50%}
.copyright{height:32px;background:var(--darker);color:#aaa;font-size:11px;text-align:center;line-height:32px}
</style>
</head>
<body>

<section class="hero">
  <div class="hero-photo" role="img" aria-label="Photo of a bookkeeper working at a laptop in a bright office"></div>
  <div class="hero-shade"></div>
  <div class="brand">
    <div class="brand-name"><i></i>Petalbooks</div>
    <div class="brand-tag">Full Service Bookkeeping for Florists</div>
  </div>
  <nav class="nav">
    <div class="nav-main">Clients &nbsp;|&nbsp; Blog &nbsp;|&nbsp; Contact</div>
    <div class="nav-sub"><span>My Account</span><span>Remote Support</span></div>
  </nav>
  <svg class="play" width="40" height="40" viewBox="0 0 40 40"><circle cx="20" cy="20" r="19" fill="#fff"/><path d="M16 12 L28 20 L16 28 Z" fill="#333"/></svg>
  <h1 class="hero-title">MAKE YOUR BOOKKEEPING SERVICE WITH US</h1>
</section>

<section class="why">
  <h2 class="section-title">Why <span>Petalbooks</span></h2>
  <div class="lead">
    <p>We'll say not! You chose a path of a sole proprietor and self employment to make money, not waste it spending time sifting through receipts, processing invoices to your vendors, and preparing statements for your tax preparer. Your time can be better spent growing your business, not bookkeeping for your business.</p>
    <p>Although we can't proudly call ourselves designers, we've been in the floral industry for many years – wearing buckets, cutting stems, stocking coolers, delivering flowers, not to mention the sleepless holidays. Bookkeeping for a family flower shop started as a hobby, but transformed into an obsession. We understand the hard work and dedication that it takes to operate a successful flower shop and the profitability metrics every shop should strive to meet.</p>
    <p>Let us manage the chaos of bookkeeping so you can focus on customer satisfaction and business growth!</p>
  </div>
  <div class="btn-row"><span class="btn">Get Your Quote</span><span class="btn">Sign-Up</span></div>
</section>

<section class="how">
  <h2 class="section-title">Here's <span>How It Works</span></h2>
  <div class="video" role="img" aria-label="Explainer video still of a presenter in a library">
    <svg width="40" height="40" viewBox="0 0 40 40"><circle cx="20" cy="20" r="19" fill="#fff"/><path d="M16 12 L28 20 L16 28 Z" fill="#333"/></svg>
  </div>
  <div class="lead">
    <p>We tried hard to make this really simple!</p>
    <p>After joining our team, we'll send you a scanner and we'll set you up. You simply scan your receipts, bills, &amp; pay invoices to us and we'll send you financial statements in the intervals you need them. Although we won't be printing and sending your bill payments, we'll send them to our payment processor where you'll log in and approve each bill – keeping you in full control of your bank account.</p>
    <p>Any opportunity we see to save you money, we'll reach out and let you know.</p>
    <p>It really is that simple!</p>
  </div>
  <div class="btn-row"><span class="btn">Get Your Quote</span><span class="btn">Sign-Up</span></div>
</section>

<section class="services">
  <h2 class="section-title">What <span>We Do</span></h2>
  <div class="service-grid">
    <div class="service-card"><div class="service-icon" role="img" aria-label="Illustration of a ledger and documents"></div><h3>Bookkeeping</h3><p>If you send us a receipt, it'll be attached to its respective accounting transaction. Audit proofing your books is our goal.</p></div>
    <div class="service-card"><div class="service-icon" role="img" aria-label="Illustration of a paycheck"></div><h3>Payroll</h3><p>Paychecks &amp; payroll taxes guaranteed error-free. If there's ever an issue, we will represent you before the IRS.</p></div>
    <div class="service-card"><div class="service-icon" role="img" aria-label="Illustration of a percent badge"></div><h3>Sales Tax</h3><p>We'll update tax rates when they change. Sales tax deposits and tax filings guaranteed error and penalty free.</p></div>
    <div class="service-card"><div class="service-icon" role="img" aria-label="Illustration of a statement report"></div><h3>Financial Statements</h3><p>Financial statements tell your story. let us help you make it a good one. With our metrics, you'll know where you can save money!</p></div>
    <div class="service-card"><div class="service-icon" role="img" aria-label="Illustration of a bill with a location pin"></div><h3>Accounts Payable</h3><p>Send us your bills and invoices, we'll account for them and let you know when they are ready for your approval. You keep control of your bank account!</p></div>
    <div class="service-card"><div class="service-icon" role="img" aria-label="Illustration of a bank building"></div><h3>Reconciliations</h3><p>One account or five, no worries – they're all included. We'll make sure that all of your expenses are accounted for.</p></div>
  </div>
  <div class="btn-row"><span class="btn">More Services</span></div>
</section>

<section class="outsourced">
  <h2 class="section-title">Outsourced Bookkeeping? <span>Whoa!</span></h2>
  <div class="lead">
    <p>Yeah, thanks to the cloud – it's a thing!</p>
    <p>In-house bookkeeping can become expensive – and although that bookkeeper sitting in your office doesn't seem to deliver too much, there are costs associated with that space, equipment and software they are using. Think of the things you can do with that space, perhaps there is a need to expand your work space, or it's a perfect location for a new floral designer that can generate income, not an expense!</p>
    <p>Let's not even talk about employing a full-time bookkeeper!</p>
    <p>According to the Bureau of Labor Statistics, the median annual wage for a bookkeeper was $38,990 in May 2016. Unless your shop's annual revenue is well above $2 million dollars, employing a full-time bookkeeper is not cost effective. That doesn't even factor any other associated costs related to industry specific training.</p>
    <p>An outsourced bookkeeper can work in their own space and use their own equipment, thus saving your time and money (isn't that the goal?)</p>
  </div>
</section>

<section class="cost">
  <h2 class="section-title">So, What Does It <span>Cost You Say?!</span></h2>
  <div class="lead">
    <p>Slow down! We'll get there. First let's talk about what you get and how easy with Petalbooks.</p>
    <p>We want you to rest assured that our costs to you will remain fixed for the term of our agreement and for only the services you need. That's right, no surprise fees or added billable hours! You pay for only the services you need.</p>
    <p>Once you become our client, you'll get a:</p>
  </div>
  <div class="cost-items">
    <div class="cost-item"><div class="cost-icon" role="img" aria-label="Illustration of a document scanner"></div>A DeskScan 500<br>Scanner</div>
    <div class="cost-item"><div class="cost-icon" role="img" aria-label="Illustration of accounting software on screens"></div>Accounting Software<br>Subscription</div>
    <div class="cost-item"><div class="cost-icon" role="img" aria-label="Illustration of map pins"></div>Accounts Payable<br>Subscription</div>
    <div class="cost-item"><div class="cost-icon" role="img" aria-label="Illustration of a payroll card"></div>Payroll Subscription</div>
  </div>
  <div class="lead"><p>Alright, alright! Now that you know what you won't have to pay, it's time to customize your quote and close the deal!</p></div>
</section>

<section class="pricing">
  <h2 class="section-title">Pricing <span>Table</span></h2>
  <div class="price-grid">
    <div class="price-card"><div class="price-head basic" role="img" aria-label="Photo of red flowers with the Basic plan title">BASIC</div><ul><li>Book Keeping</li><li>Payroll</li><li>Sales Tax</li><li>Financial Statements</li><li>Accounts Scalable</li></ul><span class="buy">BUY NOW</span></div>
    <div class="price-card"><div class="price-head standard" role="img" aria-label="Photo of office papers with the Standard plan title">STANDARD</div><ul><li>Book Keeping</li><li>Payroll</li><li>Sales Tax</li><li>Financial Statements</li><li>Accounts Scalable</li></ul><span class="buy">BUY NOW</span></div>
    <div class="price-card"><div class="price-head premium" role="img" aria-label="Photo of a desk with charts with the Premium plan title">PREMIUM</div><ul><li>Book Keeping</li><li>Payroll</li><li>Sales Tax</li><li>Financial Statements</li><li>Accounts Scalable</li></ul><span class="buy">BUY NOW</span></div>
  </div>
</section>

<section class="convince">
  <h2 class="section-title">Still Not <span>Convinced?</span></h2>
  <div class="lead">
    <p>Then we can only assume that you are a trying underneath a pile of receipts!</p>
    <p>No worries, we can set aside for that, let us create a free one-time service profitability report for you. That's right FREE, this one is on us.</p>
  </div>
  <form class="quote-form">
    <div class="field">Shop Name</div>
    <div class="field">Website Address</div>
    <div class="field">Your Name</div>
    <div class="field">Telephone Number</div>
    <div class="field">E-mail</div>
    <div class="submit">SUBMIT</div>
  </form>
  <div class="dropzone">Drag &amp; Drop Your Statement Here</div>
</section>

<section class="partners">
  <div class="partner"><i></i>Ledgerly</div>
  <div class="partner">Paywise</div>
  <div class="partner">Docstack</div>
  <div class="partner"><i></i>Shiftly</div>
</section>

<section class="blog">
  <div class="blog-head"><h2>RECENT BLOG</h2><div class="dots"><i></i><i></i><i></i><i></i></div></div>
  <div class="blog-grid">
    <article class="post"><div class="post-img p1" role="img" aria-label="Photo of a person working with papers and a calculator"></div><div class="post-body"><h4>FINANCIAL STATEMENT</h4><p>A short look at the reports every flower shop owner should read each month and what they say about profit.</p><span class="read">Read More</span></div></article>
    <article class="post"><div class="post-img p2" role="img" aria-label="Photo of a row of binders"></div><div class="post-body"><h4>PAYROLL PROCESS</h4><p>How payroll works from timesheet to paycheck, and how we keep every tax deposit on time for your team.</p><span class="read">Read More</span></div></article>
    <article class="post"><div class="post-img p3" role="img" aria-label="Photo of a pen resting on documents"></div><div class="post-body"><h4>ACCOUNTS STATEMENT</h4><p>Tips for keeping vendor bills organised and approving payments quickly without losing control of cash.</p><span class="read">Read More</span></div></article>
  </div>
</section>

<footer>
  <div class="footer">
    <div class="footer-col"><h4>Company</h4><ul><li>About Us</li><li>Press</li><li>Careers</li><li>Partner Blog</li></ul></div>
    <div class="footer-col"><h4>Information</h4><ul><li>Terms of Service</li><li>Privacy Policy</li><li>Hiring Headquarters</li><li>Online Work Report</li></ul></div>
    <div class="footer-col"><h4>Connect With Us</h4><ul><li>Contact &amp; Support</li><li>Partners</li><li>API Center</li><li>Mobile App</li></ul></div>
    <div class="footer-col"><h4>Newsletter Subscription</h4><div class="subscribe">Enter Email <svg width="12" height="12" viewBox="0 0 12 12"><path d="M1 6 L11 1 L8 11 L6 7 Z" fill="#555"/></svg></div><div class="socials"><i></i><i></i><i></i><i></i></div></div>
  </div>
  <div class="copyright">© Petalbooks. All Rights Reserved.</div>
</footer>

</body>
</html>
```